Brightlane Rapid Rinse Web Design

We are looking for a web design that highlights our state of the art fully automated commercial vehicle washing equipment. Similar system to a car wash however this system is meant for the largest vehicles on our roadways. Transport trucks with or without a trailer, busses both highway and school, RV's from 5th wheel type to A Class. Cement trucks, dump trucks, vac trucks, fuel trucks etc. Pick ups with utility trailers...Refrigerator truck clean outs.
Brightlane Rapid Rinse will wash your vehicle quickly and with a minimal impact on the environment

Home page
About us
Why Brightlane
Services and pricing
Videos of wash system
Fleets
contact us

Target Market(s)

Commercial vehicle owners and operators as well as corporate fleets. Includes busses, municipal, school and highway.both school and

Industry/Entity Type

transportation

Coding

Coded - Design and coding required

Number of Pages Required

5+ page

Font styles to use
Sans Serif

Colors
0054AA
0677BA
7BADD7
CADEEF
E8F1F8

Requirements
Must have
• Welcome page,why us page which describes the financial and environmental benefits. payment processing page, contact us page, Services which is washing vehicles and greasing for commercial vehicles that want that service and grease
Nice to have
• pictures of both clean and dirty commercial vehicles ie. before and after

```html
<!DOCTYPE html>
<html lang="en">
<head>
<meta charset="utf-8">
<title>Brightlane Rapid Rinse</title>
<link rel="stylesheet" href="https://fonts.googleapis.com/css2?family=Poppins:wght@400;500;600;700&family=Roboto:wght@400;500&display=swap">
<style>
:root{
  --brand:#0054AA;
  --brand-2:#0677BA;
  --sky:#7BADD7;
  --mist:#CADEEF;
  --ice:#E8F1F8;
  --ink:#111418;
  --body:#3a3f45;
  --white:#ffffff;
  --star:#F5C518;
  --footer:#000000;
}
*{box-sizing:border-box;margin:0;padding:0}
html,body{width:1200px;height:4099px;overflow:hidden}
body{font-family:"Roboto",Arial,sans-serif;color:var(--body);background:var(--white);position:relative}
h1,h2,h3,h4,.btn,.nav,.logo{font-family:"Poppins",Arial,sans-serif}
.container{width:1002px;margin:0 auto;position:relative}
section,header,footer{position:relative;overflow:hidden}
.btn{display:inline-block;background:var(--white);color:var(--brand);font-weight:600;font-size:16px;padding:9px 11px;border-radius:2px;text-decoration:none}
.photo{display:block}

/* header */
.site-header{height:86px;background:var(--brand)}
.logo{position:absolute;left:101px;top:16px;color:var(--white);font-weight:600;font-size:20px;line-height:24px}
.logo span{display:block;font-size:15px;font-weight:500;padding-left:104px}
.nav{position:absolute;right:99px;top:20px;display:flex;align-items:center;gap:21px;font-size:15px;color:var(--white)}
.nav .btn{font-size:15px;padding:9px 11px}

/* hero */
.hero{height:600px;background:linear-gradient(100deg,#2d2f31 0%,#4b4e50 40%,#7c8286 65%,#b8bec2 85%,#8c9297 100%)}
.hero-copy{position:absolute;left:99px;top:140px;color:var(--white)}
.hero h1{font-size:42px;line-height:48px;font-weight:700;width:520px}
.hero p{font-family:"Poppins",sans-serif;font-size:19px;margin:14px 0 22px}

/* headings */
.section-title{text-align:center;font-size:31px;font-weight:600;color:var(--ink)}
.rule{width:54px;height:3px;background:var(--brand);margin:14px auto 0}

/* services */
.services{height:721px;padding-top:86px}
.services .lead{text-align:center;font-size:15px;margin-top:28px;color:var(--ink)}
.cards{display:flex;gap:32px;margin-top:35px}
.card{width:312px;text-align:center}
.card .photo{height:236px}
.card h3{font-size:19px;font-weight:600;color:var(--ink);margin:28px 0 10px}
.card p{font-size:14.5px;line-height:29px;padding:0 14px}

/* mission */
.mission{height:635px;background:linear-gradient(160deg,#0a5fbb 0%,#0054AA 45%,#0a4ea0 75%,#0b5cb5 100%)}
.mission-copy{position:absolute;left:99px;top:80px;width:470px;color:var(--white)}
.mission h2{font-size:33px;font-weight:600}
.mission .rule{margin:12px 0 0;width:52px;background:var(--white)}
.mission p{font-size:15px;line-height:29px;margin-top:18px}
.features{list-style:none;margin-top:22px}
.features li{display:flex;align-items:center;gap:16px;height:68px;margin-bottom:22px;font-family:"Poppins",sans-serif;font-weight:600;font-size:18px}
.features svg{width:68px;height:68px;flex:none}
.mission-frame{position:absolute;left:678px;top:71px;width:428px;height:430px;background:rgba(123,173,215,.28)}
.mission-photo{position:absolute;left:634px;top:100px;width:442px;height:425px;background:linear-gradient(180deg,#b6b3a6 0%,#9c9684 45%,#c9b445 70%,#8f8a7d 100%)}

/* before after */
.compare{height:668px;background:var(--ice);padding-top:62px}
.compare .section-title{font-weight:500}
.compare-row{display:flex;gap:25px;margin-top:28px;width:1002px}
.compare figure{width:489px;text-align:center}
.compare .photo{height:399px}
.compare figcaption{font-family:"Poppins",sans-serif;font-size:21px;color:var(--ink);margin-top:24px}
.arrow{position:absolute;top:2390px;width:30px;height:30px}

/* contact */
.contact{height:428px;background:linear-gradient(135deg,#0a73c2 0%,#0677BA 50%,#0f6fb8 100%);color:var(--white);text-align:center;padding-top:68px}
.contact h2{font-size:33px;font-weight:600}
.contact .rule{background:var(--white);margin-top:10px}
.contact .lead{font-size:15px;line-height:30px;width:920px;margin:18px auto 0}
.contact-row{display:flex;justify-content:space-between;margin-top:22px;font-size:15px;text-align:left}
.contact-row div{display:flex;align-items:center;gap:16px}
.contact-row svg{width:46px;height:46px;flex:none}
.contact .btn{margin-top:30px}

/* testimonials */
.testimonials{height:535px;padding-top:88px}
.testimonials .section-title{font-size:33px}
.reviews{display:flex;justify-content:center;gap:24px;margin-top:72px}
.review{width:309px;text-align:center;position:relative}
.review-box{height:191px;border-top:3px solid var(--brand);border-radius:12px;box-shadow:0 6px 18px rgba(0,0,0,.12);padding:70px 26px 0;font-size:14.5px;line-height:25px;background:var(--white)}
.avatar{position:absolute;left:110px;top:-45px;width:90px;height:90px;border-radius:50%;background:linear-gradient(180deg,#d9dde0,#a9b4bd);border:3px solid var(--white)}
.badge{position:absolute;right:2px;bottom:2px;width:24px;height:24px;border-radius:50%;background:var(--white);border:3px solid var(--brand-2)}
.reviewer{display:flex;justify-content:center;gap:20px;margin-top:26px;font-size:15px;color:var(--ink);font-weight:500}
.stars{color:var(--star);letter-spacing:1px;font-size:13px}

/* footer */
.site-footer{height:426px;background:var(--footer);color:var(--white)}
.footer-cols{position:absolute;left:97px;top:62px;display:flex}
.footer-cols h4{font-size:22px;font-weight:600;margin-bottom:6px}
.links{list-style:none;font-size:15px}
.links li{height:31px;display:flex;align-items:center;gap:12px}
.links svg{width:14px;height:14px}
.col-quick{width:227px}
.col-other{width:196px}
.col-contact{width:311px}
.col-contact .item{display:flex;align-items:center;gap:14px;font-size:15px;margin-top:20px}
.col-contact svg{width:36px;height:36px;flex:none}
.col-news p{font-size:15px;line-height:31px;width:280px;margin-top:6px}
.email-field{width:270px;border-bottom:1px solid var(--white);font-size:15px;padding:6px 2px;margin-top:4px}
.subscribe{display:inline-block;margin:30px 0 0 6px;background:var(--brand);color:var(--white);font-family:"Poppins",sans-serif;font-weight:600;font-size:17px;padding:13px 29px;border-radius:26px}
.footer-bar{position:absolute;left:97px;right:97px;top:365px;border-top:1px solid #777;padding-top:22px;font-size:15px}
.social{position:absolute;right:0;top:16px;display:flex;gap:17px}
.social span{width:24px;height:24px;border-radius:50%;background:var(--brand);display:block}
</style>
</head>
<body>

<header class="site-header">
  <div class="logo">Brightlane Rapid<span>Rinse</span></div>
  <nav class="nav">
    <span>Home</span><span>About us</span><span>Services and pricing</span><span>Videos</span><span>More &#9662;</span>
    <span class="btn">Contact Us</span>
  </nav>
</header>

<section class="hero" role="img" aria-label="Photo of a tanker truck being washed on a wet road">
  <div class="hero-copy">
    <h1>Brightlane Rapid Rinse</h1>
    <p>Speed (less than 15 minutes)</p>
    <span class="btn">Contact Us</span>
  </div>
</section>

<section class="services">
  <div class="container">
    <h2 class="section-title">Our Services</h2>
    <div class="rule"></div>
    <p class="lead">Lorem ipsum dolor sit amet, consectetur adipiscing elit, sed do eiusmod tempor incididunt ut labore et dolore magna aliqua.</p>
    <div class="cards">
      <article class="card">
        <div class="photo" role="img" aria-label="Truck inside an automated wash bay with red brushes" style="background:linear-gradient(180deg,#c9ced3 0%,#8e969c 50%,#b5323a 70%,#d5d8db 100%)"></div>
        <h3>Automated Truck Wash</h3>
        <p>A section to describe our core service, emphasizing speed and efficiency. Use a layout with dark blue headings and clear bullet points.</p>
      </article>
      <article class="card">
        <div class="photo" role="img" aria-label="Worker pressure washing trailer wheels" style="background:linear-gradient(180deg,#d8d8d4 0%,#a9a69c 45%,#6d6a63 75%,#9b9a94 100%)"></div>
        <h3>Additional Services</h3>
        <p>Detail the additional greasing service in a well-organized format with dark blue accents.</p>
      </article>
      <article class="card">
        <div class="photo" role="img" aria-label="Row of white fleet trucks parked at dusk" style="background:linear-gradient(180deg,#6b8fb8 0%,#c9b596 40%,#e3e6ea 60%,#4a5663 100%)"></div>
        <h3>Fleet Services</h3>
        <p>A special section for fleet owners, detailing our customized solutions and fleet rates, with a consistent dark blue color scheme.</p>
      </article>
    </div>
  </div>
</section>

<section class="mission">
  <div class="mission-copy">
    <h2>Our Mission</h2>
    <div class="rule"></div>
    <p>Lorem ipsum dolor sit amet, consectetur adipiscing elit, sed do eiusmod tempor incididunt ut labore et dolore magna aliqua. Ut enim ad minim veniam, nisi ut aliquip ex ea commodo consequat.</p>
    <ul class="features">
      <li><svg viewBox="0 0 68 68"><circle cx="34" cy="34" r="32" fill="none" stroke="#fff" stroke-width="2"/><g fill="none" stroke="#fff" stroke-width="2"><rect x="17" y="26" width="24" height="14"/><path d="M41 30h6l4 5v5H41z"/><circle cx="24" cy="42" r="3"/><circle cx="45" cy="42" r="3"/></g></svg>Truck Washing</li>
      <li><svg viewBox="0 0 68 68"><circle cx="34" cy="34" r="32" fill="none" stroke="#fff" stroke-width="2"/><g fill="none" stroke="#fff" stroke-width="2"><rect x="24" y="20" width="20" height="28" rx="2"/><rect x="29" y="27" width="10" height="10"/><path d="M29 20v-4M39 20v-4M29 48v4M39 48v4"/></g></svg>Advanced Technology</li>
      <li><svg viewBox="0 0 68 68"><circle cx="34" cy="34" r="32" fill="none" stroke="#fff" stroke-width="2"/><g fill="none" stroke="#fff" stroke-width="2"><circle cx="34" cy="34" r="14"/><ellipse cx="34" cy="34" rx="6" ry="14"/><path d="M20 34h28M22 27h24M22 41h24"/></g></svg>Sustainable Practices</li>
    </ul>
  </div>
  <div class="mission-frame"></div>
  <div class="mission-photo" role="img" aria-label="Yellow dump truck being sprayed with water near a hillside"></div>
</section>

<section class="compare">
  <div class="container">
    <h2 class="section-title">Before/After</h2>
    <div class="rule"></div>
    <div class="compare-row">
      <figure>
        <div class="photo" role="img" aria-label="Dirty orange refuse truck before washing" style="background:linear-gradient(180deg,#a7a8a6 0%,#b4643a 40%,#c46a34 65%,#5b5a56 100%)"></div>
        <figcaption>Before Truck</figcaption>
      </figure>
      <figure>
        <div class="photo" role="img" aria-label="Clean orange refuse truck after washing" style="background:linear-gradient(180deg,#c7c9cc 0%,#e0662a 40%,#ea6c28 65%,#77797c 100%)"></div>
        <figcaption>After Truck</figcaption>
      </figure>
    </div>
  </div>
</section>
<svg class="arrow" style="left:50px" viewBox="0 0 30 30"><circle cx="15" cy="15" r="14" fill="#fff" stroke="#111" stroke-width="1.3"/><path d="M17 9l-6 6 6 6" fill="none" stroke="#111" stroke-width="1.6"/></svg>
<svg class="arrow" style="left:1119px" viewBox="0 0 30 30"><circle cx="15" cy="15" r="14" fill="#fff" stroke="#111" stroke-width="1.3"/><path d="M13 9l6 6-6 6" fill="none" stroke="#111" stroke-width="1.6"/></svg>

<section class="contact">
  <div class="container">
    <h2>Contact US</h2>
    <div class="rule"></div>
    <p class="lead">Lorem ipsum dolor sit amet, consectetur adipiscing elit, sed do eiusmod tempor incididunt ut labore et dolore magna aliqua. Ut enim ad minim veniam, quis nostrud exercitation ullamco laboris nisi ut aliquip ex ea commodo consequat.</p>
    <div class="contact-row">
      <div><svg viewBox="0 0 46 46"><circle cx="23" cy="23" r="21.5" fill="none" stroke="#fff" stroke-width="2"/><path d="M17 14l4 4-2 3c1 3 3 5 6 6l3-2 4 4-2 3c-7 0-15-8-15-15z" fill="#fff"/></svg>+1888 8888 8888</div>
      <div><svg viewBox="0 0 46 46"><circle cx="23" cy="23" r="21.5" fill="none" stroke="#fff" stroke-width="2"/><rect x="14" y="17" width="18" height="13" fill="#fff"/><path d="M14 17l9 7 9-7" fill="none" stroke="#0677BA" stroke-width="1.6"/></svg>info@brightlanerapidrinse</div>
      <div><svg viewBox="0 0 46 46"><circle cx="23" cy="23" r="21.5" fill="none" stroke="#fff" stroke-width="2"/><path d="M23 12c-4 0-7 3-7 7 0 5 7 14 7 14s7-9 7-14c0-4-3-7-7-7z" fill="none" stroke="#fff" stroke-width="2"/><circle cx="23" cy="19" r="2.5" fill="#fff"/></svg>Brightlane Rapid Rinse,United State.</div>
    </div>
    <span class="btn">Contact Us</span>
  </div>
</section>

<section class="testimonials">
  <div class="container">
    <h2 class="section-title">Customer Testimonials</h2>
    <div class="rule"></div>
    <div class="reviews">
      <div class="review">
        <div class="avatar" role="img" aria-label="Customer portrait"><span class="badge"></span></div>
        <div class="review-box">Sed ut perspiciatis unde omnis iste natus error sit voluptatem accusantium doloremque laudantium, totam rem aperiam, eaque ipsa</div>
        <div class="reviewer"><span>Jhon Deo</span><span class="stars">★★★★★</span></div>
      </div>
      <div class="review">
        <div class="avatar" role="img" aria-label="Customer portrait"><span class="badge"></span></div>
        <div class="review-box">Sed ut perspiciatis unde omnis iste natus error sit voluptatem accusantium doloremque laudantium, totam rem aperiam, eaque ipsa</div>
        <div class="reviewer"><span>Jhon Deo</span><span class="stars">★★★★★</span></div>
      </div>
      <div class="review">
        <div class="avatar" role="img" aria-label="Customer portrait"><span class="badge"></span></div>
        <div class="review-box">Sed ut perspiciatis unde omnis iste natus error sit voluptatem accusantium doloremque laudantium, totam rem aperiam, eaque ipsa</div>
        <div class="reviewer"><span>Jhon Deo</span><span class="stars">★★★★★</span></div>
      </div>
    </div>
  </div>
</section>

<footer class="site-footer">
  <div class="footer-cols">
    <div class="col-quick">
      <h4>Quick Links</h4>
      <ul class="links">
        <li><svg viewBox="0 0 14 14"><path d="M1 7h10M7 2l5 5-5 5" fill="none" stroke="#fff" stroke-width="2.2"/></svg>Home p</li>
        <li><svg viewBox="0 0 14 14"><path d="M1 7h10M7 2l5 5-5 5" fill="none" stroke="#fff" stroke-width="2.2"/></svg>About us</li>
        <li><svg viewBox="0 0 14 14"><path d="M1 7h10M7 2l5 5-5 5" fill="none" stroke="#fff" stroke-width="2.2"/></svg>Services and pricing</li>
        <li><svg viewBox="0 0 14 14"><path d="M1 7h10M7 2l5 5-5 5" fill="none" stroke="#fff" stroke-width="2.2"/></svg>Videos</li>
        <li><svg viewBox="0 0 14 14"><path d="M1 7h10M7 2l5 5-5 5" fill="none" stroke="#fff" stroke-width="2.2"/></svg>Fleets</li>
        <li><svg viewBox="0 0 14 14"><path d="M1 7h10M7 2l5 5-5 5" fill="none" stroke="#fff" stroke-width="2.2"/></svg>contact us</li>
      </ul>
    </div>
    <div class="col-other">
      <h4>Other Links</h4>
      <ul class="links">
        <li><svg viewBox="0 0 14 14"><path d="M1 7h10M7 2l5 5-5 5" fill="none" stroke="#fff" stroke-width="2.2"/></svg>FAQ</li>
        <li><svg viewBox="0 0 14 14"><path d="M1 7h10M7 2l5 5-5 5" fill="none" stroke="#fff" stroke-width="2.2"/></svg>Tems of Use</li>
        <li><svg viewBox="0 0 14 14"><path d="M1 7h10M7 2l5 5-5 5" fill="none" stroke="#fff" stroke-width="2.2"/></svg>Privacy Policy</li>
        <li><svg viewBox="0 0 14 14"><path d="M1 7h10M7 2l5 5-5 5" fill="none" stroke="#fff" stroke-width="2.2"/></svg>Support Links</li>
        <li><svg viewBox="0 0 14 14"><path d="M1 7h10M7 2l5 5-5 5" fill="none" stroke="#fff" stroke-width="2.2"/></svg>Conditions</li>
      </ul>
    </div>
    <div class="col-contact">
      <h4>Contact Us</h4>
      <div class="item"><svg viewBox="0 0 36 36"><circle cx="18" cy="18" r="18" fill="#0054AA"/><path d="M18 10c-3 0-5 2-5 5 0 4 5 10 5 10s5-6 5-10c0-3-2-5-5-5z" fill="#fff"/><circle cx="18" cy="15" r="1.8" fill="#0054AA"/></svg>Company Name,United State.</div>
      <div class="item"><svg viewBox="0 0 36 36"><circle cx="18" cy="18" r="18" fill="#0054AA"/><rect x="11" y="12" width="14" height="11" fill="#fff"/><path d="M11 12l7 6 7-6" fill="none" stroke="#0054AA" stroke-width="1.4"/></svg>info@brightlanemail.com</div>
      <div class="item"><svg viewBox="0 0 36 36"><circle cx="18" cy="18" r="18" fill="#0054AA"/><path d="M13 10l3 3-1.5 2.5c1 2 2.5 3.5 4.5 4.5L21.5 18.5l3 3-1.5 2.5C17.5 24 12 18.5 12 13z" fill="#fff"/></svg>+1888 8888 8888</div>
    </div>
    <div class="col-news">
      <h4>Sign Up Our Newsletter</h4>
      <p>Lorem ipsum dolor sit amet,consectetur adipiscing elit,adipiscing elit.</p>
      <div class="email-field">Email</div>
      <span class="subscribe">Subscribe</span>
    </div>
  </div>
  <div class="footer-bar">
    Copyrights@2024.Brightlane Rapid Rinse.All Rights Reserved
    <div class="social"><span></span><span></span><span></span><span></span></div>
  </div>
</footer>

</body>
</html>
```